Coastline Premier Retreats Business Card Design

Design a business card for Coastline Premier Retreats. Look at the website for colors and reference. Card should have logo, name, title, office number, mobile number, email, URL and a tagline like, "Luxury Hotel & Resort Email Marketing" (This might change).

https://www.coastlinepremierretreats.example

The rest I will leave up to your imagination.

Contact Information for Business Card

Logo, name, title, office number, mobile number, email, URL and a tagline like, "Luxury Hotel & Resort Email Marketing" (This might change).

```html
<!DOCTYPE html>
<html lang="en">
<head>
<meta charset="utf-8">
<title>Coastline Premier Retreats – Business Card</title>
<link rel="stylesheet" href="https://fonts.googleapis.com/css2?family=Arimo:wght@400;700&display=swap">
<style>
  :root {
    --page-bg: #2b2b2b;
    --card-bg: #1b1b1b;
    --accent: #f07a16;
    --text-light: #f2f2f2;
    --text-muted: #e2e2e2;
  }
  * { box-sizing: border-box; margin: 0; padding: 0; }
  html, body {
    width: 1200px; height: 900px; overflow: hidden;
    background: var(--page-bg);
    font-family: "Arimo", Arial, sans-serif;
  }
  .sheet {
    width: 1200px; height: 900px;
    display: flex; flex-direction: column; align-items: center; justify-content: center;
    gap: 40px;
  }
  .card {
    position: relative;
    width: 700px; height: 400px;
    background: var(--card-bg);
    border-bottom: 5px solid var(--accent);
    border-left: 3px solid var(--accent);
    box-shadow: 0 10px 30px rgba(0,0,0,.45);
  }
  .brand-name {
    color: var(--text-light);
    font-weight: 700;
    text-transform: uppercase;
    letter-spacing: .06em;
    line-height: 1.1;
    display: flex; align-items: center; gap: 14px;
  }
  .brand-mark {
    width: 14px; height: 14px; background: var(--accent); flex: none;
  }
  /* front */
  .card-front { display: flex; align-items: center; justify-content: center; }
  .card-front .brand-name { font-size: 40px; }
  /* back */
  .card-back .brand-name {
    position: absolute; left: 60px; top: 150px;
    font-size: 22px; width: 240px;
  }
  .divider {
    position: absolute; left: 345px; top: 70px;
    width: 1px; height: 210px; background: var(--accent);
  }
  .contact {
    position: absolute; left: 375px; top: 62px;
    color: var(--text-muted); font-size: 15px; line-height: 1.3;
  }
  .person-name {
    color: var(--accent); font-weight: 700; font-size: 28px;
    text-transform: uppercase; letter-spacing: .01em;
  }
  .person-title { margin-bottom: 16px; font-size: 15px; }
  .address { margin-bottom: 14px; }
  .contact-list { list-style: none; }
  .contact-list li { display: flex; align-items: center; gap: 8px; }
  .contact-list svg { width: 12px; height: 12px; flex: none; }
  .tagline {
    position: absolute; left: 0; right: 0; bottom: 36px;
    text-align: center; color: var(--text-light); font-size: 18px;
  }
</style>
</head>
<body>
<main class="sheet">
  <section class="card card-front" aria-label="Card front">
    <div class="brand-name"><span class="brand-mark"></span>Coastline Premier Retreats</div>
  </section>

  <section class="card card-back" aria-label="Card back">
    <div class="brand-name"><span class="brand-mark"></span>Coastline Premier Retreats</div>
    <div class="divider"></div>
    <div class="contact">
      <p class="person-name">Daniel Marsh</p>
      <p class="person-title">CEO/Founder</p>
      <p class="address">Po Box, 218 B Shore Rd<br>Harbor View, CA 93012</p>
      <ul class="contact-list">
        <li><svg viewBox="0 0 12 12"><rect x="3" y="1" width="6" height="10" rx="1" fill="none" stroke="#f07a16" stroke-width="1.2"/></svg>555.214.7300</li>
        <li><svg viewBox="0 0 12 12"><path d="M1 5 Q6 1 11 5 L9 6 L8 4.5 L4 4.5 L3 6 Z M3 7 H9 V10 H3 Z" fill="#f07a16"/></svg>+34 600 555 214</li>
        <li><svg viewBox="0 0 12 12"><rect x="1" y="2.5" width="10" height="7" fill="#f07a16"/><path d="M1 2.5 L6 6.5 L11 2.5" fill="none" stroke="#1b1b1b" stroke-width="1"/></svg>info@coastlinepremierretreats.example</li>
        <li><svg viewBox="0 0 12 12"><circle cx="6" cy="6" r="5" fill="#f07a16"/><path d="M1 6 H11 M6 1 Q3 6 6 11 Q9 6 6 1" fill="none" stroke="#1b1b1b" stroke-width=".8"/></svg>www.coastlinepremierretreats.example</li>
      </ul>
    </div>
    <p class="tagline">Luxury Hotel &amp; Resort Email Marketing</p>
  </section>
</main>
</body>
</html>
```